Brightmill Data Works

Our company is about IT hardwares and IT solutions. IT hardware such as PC, RAMS, storage and servers. IT solutions such as project management, BA. We are also selling new technology too.

Target Market(s)

Consumer, Small to Medium Business, Corporate

Requirements
Must have
• The business card must have the following:
• Name:
• Title:
• Contact Number:
• Email address:
• Website:
• Color: Must match the logo color upgrade

```html
<!DOCTYPE html>
<html lang="en">
<head>
<meta charset="utf-8">
<title>Brightmill Data Works – Business Card</title>
<link href="https://fonts.googleapis.com/css2?family=Saira+Semi+Condensed:wght@400;700&display=swap" rel="stylesheet">
<style>
  :root {
    --copper: #a8622a;
    --slate: #706e6e;
    --paper: #d4d6d6;
    --ink: #363636;
    --mist: #dadada;
    --backdrop: #dcdcdc;
  }
  * { margin: 0; padding: 0; box-sizing: border-box; }
  html, body { width: 1200px; height: 878px; overflow: hidden; }
  body {
    background: var(--backdrop);
    font-family: "Saira Semi Condensed", "Arial Narrow", sans-serif;
    position: relative;
  }
  .card {
    position: absolute;
    top: 139px;
    width: 339px;
    height: 597px;
    overflow: hidden;
  }
  .card--front { left: 230px; background: var(--copper); }
  .card--back { left: 598px; background: linear-gradient(160deg, #dadcdc, var(--paper)); }
  .card svg.shape { position: absolute; inset: 0; }
  .brand-dot {
    position: absolute;
    left: 50%;
    width: 28px;
    height: 28px;
    border-radius: 50%;
    transform: translateX(-50%);
  }
  .card--front .brand-dot { top: 232px; background: var(--copper); }
  .card--back .brand-dot { top: 56px; background: var(--mist); }
  .wordmark {
    position: absolute;
    left: 0;
    width: 100%;
    text-align: center;
    font-weight: 700;
    font-size: 42px;
    line-height: 40px;
    letter-spacing: 0.5px;
    text-transform: uppercase;
  }
  .card--front .wordmark { top: 282px; color: var(--mist); }
  .card--back .wordmark { top: 112px; color: var(--ink); }
  .details {
    position: absolute;
    left: 0;
    width: 100%;
    text-align: center;
  }
  .person-name {
    position: absolute;
    top: 310px;
    width: 100%;
    font-size: 33px;
    line-height: 34px;
    color: var(--ink);
    text-transform: uppercase;
  }
  .person-title {
    position: absolute;
    top: 344px;
    width: 100%;
    font-size: 27px;
    line-height: 28px;
    color: var(--copper);
    text-transform: uppercase;
  }
  .contact {
    position: absolute;
    top: 428px;
    width: 100%;
    list-style: none;
    font-size: 25px;
    line-height: 38px;
    color: #1e1e1e;
    letter-spacing: 0.4px;
  }
</style>
</head>
<body>
  <section class="card card--front" aria-label="Card front">
    <svg class="shape" width="339" height="597" viewBox="0 0 339 597" aria-hidden="true">
      <path d="M0 64 C40 50 80 52 120 60 S260 96 339 86 L339 540 C280 550 200 532 140 516 S40 500 0 514 Z" fill="var(--slate)"/>
    </svg>
    <span class="brand-dot" aria-hidden="true"></span>
    <h1 class="wordmark">Brightmill<br>Data Works</h1>
  </section>

  <section class="card card--back" aria-label="Card back">
    <svg class="shape" width="339" height="597" viewBox="0 0 339 597" aria-hidden="true">
      <path d="M0 0 H339 V225 Q170 295 0 217 Z" fill="var(--copper)"/>
    </svg>
    <span class="brand-dot" aria-hidden="true"></span>
    <h2 class="wordmark">Brightmill<br>Data Works</h2>
    <div class="details">
      <p class="person-name">Dana Whitfield</p>
      <p class="person-title">Manager</p>
      <ul class="contact">
        <li>+1-555-014-2087</li>
        <li>dana@brightmill.com</li>
        <li>www.brightmill.com</li>
      </ul>
    </div>
  </section>
</body>
</html>
```